New Company Business Card design

Looking for a corporate looking business card utilising my new logo design - the logo i would like embossed as one option and flat as another - simplistic but stylish - less is more - we are an import export business launching into the market - i would like a couple of options as main background - Grey or Black

```html
<!DOCTYPE html>
<html lang="en">
<head>
<meta charset="utf-8">
<title>Tradewell Global Supply – Business Card</title>
<link href="https://fonts.googleapis.com/css2?family=Arimo:wght@400;700&display=swap" rel="stylesheet">
<style>
  :root {
    --backdrop: #d9c9b8;
    --paper: #f7f7f5;
    --brand-blue: #1877c4;
    --card-black: #262626;
    --ink: #111111;
    --muted-grey: #6f6f6f;
    --tagline-grey: #8a8a8a;
  }
  * { box-sizing: border-box; margin: 0; padding: 0; }
  html, body { width: 1200px; height: 848px; overflow: hidden; }
  body {
    background: var(--backdrop);
    font-family: "Arimo", Arial, sans-serif;
    position: relative;
  }
  .card {
    position: absolute;
    width: 620px;
    height: 354px;
    overflow: hidden;
  }
  .card-front {
    left: 230px; top: 50px;
    background: var(--paper);
    display: flex; flex-direction: column; align-items: center; justify-content: center;
  }
  .brand-lockup { display: flex; align-items: center; gap: 18px; }
  .brand-dot {
    width: 46px; height: 46px; border-radius: 50%;
    background: var(--brand-blue);
  }
  .brand-name {
    font-size: 64px; font-weight: 700; color: var(--brand-blue);
    letter-spacing: 1px;
  }
  .front-url {
    margin-top: 34px;
    font-size: 15px; color: var(--muted-grey); letter-spacing: 0.3px;
  }
  .card-back {
    left: 350px; top: 444px;
  }
  .card-back svg.split { position: absolute; inset: 0; }
  .contact {
    position: absolute; left: 40px; top: 98px; color: var(--ink);
  }
  .contact-name { font-size: 21px; font-weight: 700; letter-spacing: 0.5px; }
  .contact-role { font-size: 15px; font-weight: 700; margin-top: 2px; }
  .contact-address { font-size: 15px; line-height: 1.3; margin-top: 16px; }
  .contact-list { list-style: none; margin-top: 12px; font-size: 15px; }
  .contact-list li { display: flex; align-items: center; gap: 12px; height: 21px; }
  .contact-list svg { width: 13px; height: 13px; flex: none; }
  .back-brand {
    position: absolute; right: 44px; top: 128px; text-align: center; width: 250px;
  }
  .back-brand-row { display: flex; align-items: center; justify-content: center; gap: 10px; }
  .back-brand-dot { width: 22px; height: 22px; border-radius: 50%; background: var(--brand-blue); }
  .back-brand-name { font-size: 34px; font-weight: 700; color: var(--brand-blue); }
  .back-brand-full {
    font-size: 14px; font-weight: 700; color: var(--brand-blue); letter-spacing: 1px;
    margin-top: 8px; border-bottom: 1px solid var(--brand-blue); padding-bottom: 4px;
  }
  .back-tagline {
    font-size: 9px; color: var(--tagline-grey); letter-spacing: 1.4px; margin-top: 5px;
  }
</style>
</head>
<body>

<section class="card card-front">
  <div class="brand-lockup">
    <span class="brand-dot"></span>
    <span class="brand-name">TRADEWELL</span>
  </div>
  <p class="front-url">www.tradewellglobalsupply.com</p>
</section>

<section class="card card-back">
  <svg class="split" viewBox="0 0 620 354" preserveAspectRatio="none">
    <rect width="620" height="354" fill="var(--card-black)"/>
    <path d="M0 0 H330 L250 354 H0 Z" fill="var(--brand-blue)"/>
  </svg>

  <div class="contact">
    <p class="contact-name">DANIEL REYES</p>
    <p class="contact-role">CEO/FOUNDER</p>
    <p class="contact-address">2149 Harbor View Road<br>Juneau, Alaska 99801</p>
    <ul class="contact-list">
      <li><svg viewBox="0 0 16 16"><path d="M4 1l3 3-2 2c1 2 3 4 5 5l2-2 3 3-2 3C7 15 1 9 1 3z" fill="var(--ink)"/></svg>555 218 4407</li>
      <li><svg viewBox="0 0 16 16"><rect x="4" y="1" width="8" height="14" rx="1.5" fill="none" stroke="var(--ink)" stroke-width="2"/></svg>555 736 1920</li>
      <li><svg viewBox="0 0 16 16"><rect x="4" y="1" width="8" height="5" fill="var(--ink)"/><rect x="1" y="6" width="14" height="7" rx="1" fill="var(--ink)"/></svg>555 402 6618</li>
      <li><svg viewBox="0 0 16 16"><rect x="1" y="3" width="14" height="10" rx="1" fill="var(--ink)"/><path d="M1 4l7 5 7-5" fill="none" stroke="var(--brand-blue)" stroke-width="1.5"/></svg>hello@tradewell.com</li>
      <li><svg viewBox="0 0 16 16"><circle cx="8" cy="8" r="7" fill="var(--ink)"/><path d="M1 8h14M8 1c-3 4-3 10 0 14M8 1c3 4 3 10 0 14" fill="none" stroke="var(--brand-blue)" stroke-width="1"/></svg>www.tradewell.com</li>
    </ul>
  </div>

  <div class="back-brand">
    <div class="back-brand-row">
      <span class="back-brand-dot"></span>
      <span class="back-brand-name">TRADEWELL</span>
    </div>
    <p class="back-brand-full">TRADEWELL GLOBAL SUPPLY</p>
    <p class="back-tagline">WORLDWIDE SUPPLY FOR LOCAL DEMAND</p>
  </div>
</section>

</body>
</html>
```